TALMORK

The business want a professional looking business card. We have a scetch we will add but want the extra upgrade, and would like more suggestions for variations of our business cards.

```html
<!DOCTYPE html>
<html lang="en">
<head>
<meta charset="utf-8">
<title>TALMORK – Business Card</title>
<link href="https://fonts.googleapis.com/css2?family=Cormorant+Garamond:wght@500;600;700&family=EB+Garamond:wght@400&family=Didact+Gothic&family=Montserrat:wght@500&display=swap" rel="stylesheet">
<style>
  :root {
    --page: #f1f1f0;
    --card: #1d1d1f;
    --gold: #c7a66a;
    --gold-light: #f1e3c6;
    --label: #1a1a1a;
  }
  * { margin: 0; padding: 0; box-sizing: border-box; }
  html, body { width: 1200px; height: 670px; overflow: hidden; background: var(--page); }
  .canvas { position: relative; width: 1200px; height: 670px; }

  .card {
    position: absolute; top: 178px; width: 493px; height: 314px;
    background: var(--card); overflow: hidden;
  }
  .card--front { left: 72px; }
  .card--back { left: 636px; }

  .rule { position: absolute; background: var(--gold); }
  .rule--vertical { left: 30px; top: 0; width: 1px; height: 100%; }
  .rule--horizontal { left: 0; top: 140px; width: 100%; height: 1px; }

  .company-title {
    position: absolute; left: 40px; top: 46px;
    font-family: "Cormorant Garamond", serif; font-weight: 700;
    font-size: 40px; line-height: 1; color: var(--gold-light); letter-spacing: 0.5px;
  }
  .person-name {
    position: absolute; left: 42px; top: 93px;
    font-family: "EB Garamond", serif; font-size: 21px; color: var(--gold);
  }
  .role {
    position: absolute; left: 42px; top: 166px;
    font-family: "Didact Gothic", sans-serif; font-size: 23px; color: var(--gold);
  }
  .contacts { position: absolute; left: 40px; top: 202px; list-style: none; }
  .contacts li {
    display: flex; align-items: center; height: 28px;
    font-family: "Didact Gothic", sans-serif; font-size: 17.5px; color: var(--gold-light);
  }
  .contacts svg { width: 18px; height: 18px; margin-right: 12px; flex: none; }
  .front-wordmark {
    position: absolute; right: 20px; top: 278px;
    font-family: "Cormorant Garamond", serif; font-weight: 600;
    font-size: 17px; letter-spacing: 4px; color: var(--gold);
  }

  .back-mark {
    position: absolute; left: 50%; top: 80px; width: 80px; height: 80px;
    margin-left: -40px; border-radius: 50%; background: var(--gold);
  }
  .back-wordmark {
    position: absolute; left: 0; right: 0; top: 196px; text-align: center;
    font-family: "Cormorant Garamond", serif; font-weight: 600;
    font-size: 38px; letter-spacing: 11px; padding-left: 11px; color: var(--gold);
  }
  .since {
    position: absolute; left: 0; right: 0; top: 243px; text-align: center;
    font-family: "Didact Gothic", sans-serif; font-size: 12px;
    letter-spacing: 5px; padding-left: 5px; color: var(--gold);
  }

  .side-label {
    position: absolute; top: 536px; width: 493px; text-align: center;
    font-family: "Montserrat", sans-serif; font-weight: 500; font-size: 21px;
    letter-spacing: 0.5px; color: var(--label);
  }
  .side-label--front { left: 72px; }
  .side-label--back { left: 636px; }
</style>
</head>
<body>
<main class="canvas">
  <section class="card card--front" aria-label="Front of business card">
    <div class="rule rule--vertical"></div>
    <div class="rule rule--horizontal"></div>
    <h1 class="company-title">TALMORK LINDVIK</h1>
    <p class="person-name">Aksel Morten Lindvik</p>
    <p class="role">CEO &amp; Founder</p>
    <ul class="contacts">
      <li>
        <svg viewBox="0 0 18 18" aria-hidden="true"><rect x="4.5" y="1" width="9" height="16" rx="1.6" fill="none" stroke="#c7a66a" stroke-width="1.5"/><circle cx="9" cy="14.2" r="0.9" fill="#c7a66a"/></svg>
        004795517302
      </li>
      <li>
        <svg viewBox="0 0 18 18" aria-hidden="true"><rect x="1" y="4" width="16" height="11" fill="#c7a66a"/><path d="M1 4 L9 10.5 L17 4 M1 15 L7 9 M17 15 L11 9" fill="none" stroke="#1d1d1f" stroke-width="1.2"/></svg>
        talmork.llc@mailpost.com
      </li>
      <li>
        <svg viewBox="0 0 18 18" aria-hidden="true"><circle cx="9" cy="9" r="7.5" fill="none" stroke="#c7a66a" stroke-width="1.3"/><ellipse cx="9" cy="9" rx="3.3" ry="7.5" fill="none" stroke="#c7a66a" stroke-width="1"/><path d="M1.5 9 H16.5 M3 5 H15 M3 13 H15" stroke="#c7a66a" stroke-width="1"/></svg>
        www.talmork.llc
      </li>
    </ul>
    <div class="front-wordmark">TALMORK</div>
  </section>

  <section class="card card--back" aria-label="Back of business card">
    <div class="back-mark"></div>
    <div class="back-wordmark">TALMORK</div>
    <div class="since">SINCE 2026</div>
  </section>

  <p class="side-label side-label--front">FRONT CARD</p>
  <p class="side-label side-label--back">BACK CARD</p>
</main>
</body>
</html>
```